One of a Kind Clean Business Card

We need to design a new business card template for our company. Our company designs and produced merchandising displays. You can see a sample of what we produce on our site www.qorvanexhibits.net. I have uploaded our logo in vector format, as well as a picture of our current business cards. We want a totally different look. We want simple and clean, looking forward to seeing what people create.
Updates

I would like to update the address for Qorvan Display Group Inc. 518 E Tollmere Ln Arlington Heights, IL 60017 Would also note. No QR codes

Industry/Entity Type

Business

Contact Information for Business Card

Need a 1 sided business card designed.

Font styles to use
Serif

Requirements
Must have
• Easy to view; Clean Design
Nice to have
• Features that promote engineering and creativity
Should not have
• Too much clutter, keep it simple

```html
<!DOCTYPE html>
<html lang="en">
<head>
<meta charset="utf-8">
<title>Qorvan Display Group Inc. – Business Card</title>
<link href="https://fonts.googleapis.com/css2?family=Source+Serif+4:wght@400;600&display=swap" rel="stylesheet">
<style>
  :root {
    --backdrop: #ece9e6;
    --card: #ffffff;
    --maroon: #6e2530;
    --ink: #222222;
    --sheen: #8a3a45;
  }
  html, body {
    margin: 0;
    width: 1200px;
    height: 1000px;
    overflow: hidden;
    background: var(--backdrop);
  }
  .business-card {
    position: absolute;
    left: 180px;
    top: 260px;
    width: 840px;
    height: 480px;
    background: var(--card);
    box-shadow: 0 10px 30px rgba(0,0,0,0.12);
    font-family: "Source Serif 4", serif;
    color: var(--ink);
  }
  .holder-name {
    position: absolute;
    left: 64px;
    top: 56px;
    margin: 0;
    font-size: 34px;
    font-weight: 600;
    letter-spacing: 0.5px;
    color: var(--maroon);
  }
  .contact-list {
    position: absolute;
    left: 64px;
    top: 196px;
    margin: 0;
    padding: 0;
    list-style: none;
    font-size: 20px;
    line-height: 29px;
    letter-spacing: 0.4px;
  }
  .contact-list li {
    display: flex;
    align-items: center;
  }
  .contact-icon {
    width: 16px;
    height: 16px;
    margin-right: 14px;
    fill: var(--maroon);
    stroke: var(--maroon);
  }
  .mailing-address {
    position: absolute;
    left: 64px;
    top: 318px;
    margin: 0;
    font-style: normal;
    font-size: 20px;
    line-height: 29px;
    letter-spacing: 0.4px;
  }
  .company-name {
    position: absolute;
    right: 70px;
    bottom: 86px;
    margin: 0;
    font-size: 20px;
    font-weight: 400;
    letter-spacing: 0.4px;
    color: var(--ink);
  }
  .accent-band {
    position: absolute;
    left: 0;
    right: 0;
    bottom: 14px;
    height: 26px;
    background: linear-gradient(90deg, var(--maroon) 0%, var(--maroon) 60%, var(--sheen) 75%, var(--maroon) 90%);
  }
</style>
</head>
<body>
  <section class="business-card">
    <h1 class="holder-name">DANA RULKOWE</h1>

    <ul class="contact-list">
      <li>
        <svg class="contact-icon" viewBox="0 0 16 16" aria-hidden="true">
          <path stroke="none" d="M1 5c0-2 3-3 7-3s7 1 7 3v1h-3V5H4v1H1z"/>
          <rect x="3" y="7" width="10" height="7" rx="1" stroke="none"/>
        </svg>
        815-555-0142
      </li>
      <li>
        <svg class="contact-icon" viewBox="0 0 16 16" aria-hidden="true">
          <path stroke="none" d="M3 1l3 1-1 4 2 3 3 2 3-2 2 3-2 3C8 14 2 8 2 3z"/>
        </svg>
        312-555-0176
      </li>
      <li>
        <svg class="contact-icon" viewBox="0 0 16 16" aria-hidden="true">
          <rect x="1" y="3" width="14" height="10" stroke="none"/>
          <path d="M1 3l7 6 7-6" fill="none" stroke="#fff" stroke-width="1.3"/>
        </svg>
        drulkowe@qorvanexhibits.net
      </li>
      <li>
        <svg class="contact-icon" viewBox="0 0 16 16" aria-hidden="true">
          <circle cx="10" cy="6" r="4" fill="none" stroke-width="2"/>
          <path d="M7 9l-5 5" fill="none" stroke-width="2.5" stroke-linecap="round"/>
        </svg>
        www.qorvanexhibits.net
      </li>
    </ul>

    <address class="mailing-address">
      518 E Tollmere Ln<br>
      Arlington Heights, IL 60017
    </address>

    <p class="company-name">Qorvan Display Group Inc.</p>

    <div class="accent-band"></div>
  </section>
</body>
</html>
```